I would like a minimalist clean and uncluttered website design.
Initially, I would like to see a front page only and would then like to build on the project front there.
DVQ logo file with no background is attached, can be grey scale if the designer wishes.
I would like the front page to speak about the company's ethos and goals and I will need to put a great deal of thought into this to ensure it has the desired impact with the content on the subsequent pages.
The paragraph below gives a bit of an idea as to what this will include.
"DVQ is a technology company providing approachable IT products and services to business:
With the overwhelming advancements in technology, businesses often find it difficult to determine what is available and what best suits their businesses specific needs.
We can assist business with their IT infrustucture, devices, software in procurement, installation, training, cost control as well as ongoing administration and support. We also keep our Clients informed of new technology and products which can benefit them"
Target Market(s)
Business, Health, Education, Professional Practices. Target age would be around 30 plus either male or female. Office administration level through Managing Directors. English speaking.

```html
<!DOCTYPE html>
<html lang="en">
<head>
<meta charset="utf-8">
<title>DVQ – Approachable IT for business</title>
<link href="https://fonts.googleapis.com/css2?family=Questrial&family=Open+Sans:ital,wght@0,300;0,400;1,300&display=swap" rel="stylesheet">
<style>
:root{
  --navy:#2f3f7a;
  --navy-dark:#26346a;
  --green:#8db849;
  --text:#5c5c5c;
  --muted:#8a8a8a;
  --line:#dcdcdc;
  --footer:#f3f3f3;
  --white:#ffffff;
}
*{margin:0;padding:0;box-sizing:border-box}
html,body{width:1200px;height:1035px;overflow:hidden;background:var(--white)}
body{position:relative;font-family:'Open Sans',sans-serif;color:var(--text)}

.site-header{position:absolute;top:0;left:0;width:1200px;height:75px;border-bottom:1px solid var(--line);background:var(--white)}
.brand{position:absolute;left:155px;top:14px;display:flex;align-items:center;gap:10px;font-family:'Questrial',sans-serif;font-size:30px;color:var(--navy);letter-spacing:2px}
.brand-mark{width:30px;height:30px;background:var(--green)}
.main-nav{position:absolute;left:470px;top:0;display:flex;height:75px}
.main-nav a{font-family:'Questrial',sans-serif;font-size:15px;color:#555;text-decoration:none;line-height:72px;padding:0 22px;position:relative}
.main-nav a:first-child{padding:0 23px}
.main-nav a.active{color:var(--green)}
.main-nav a.active::after{content:"";position:absolute;left:0;right:0;bottom:-1px;height:4px;background:var(--green)}
.account{position:absolute;left:935px;top:30px;display:flex;align-items:center;font-family:'Questrial',sans-serif;font-size:11px;color:#a0a0a0}
.account span{display:flex;align-items:center;gap:3px}
.account .sep{width:1px;height:14px;background:var(--line);margin:0 12px}

.hero{position:absolute;top:75px;left:0;width:1200px;height:414px;border-bottom:1px solid var(--line)}
.hero-photo{position:absolute;inset:0;background:linear-gradient(90deg,#eef1f3 0%,#e6ebee 45%,#d9e1e8 60%,#c9d2dc 75%,#dfe6ec 100%)}
.hero-copy{position:absolute;left:151px;top:126px}
.hero-title{font-family:'Questrial',sans-serif;font-weight:400;font-size:31px;color:var(--navy);letter-spacing:-.3px}
.hero-lead{margin-top:6px;font-style:italic;font-weight:300;font-size:17px;line-height:24px;color:#6a6a6a}
.btn-more{display:inline-block;margin-top:18px;width:121px;height:33px;background:var(--green);color:var(--white);font-family:'Questrial',sans-serif;font-size:13px;line-height:33px;text-align:center;text-decoration:none}
.slider-dots{position:absolute;left:151px;top:338px;display:flex;gap:3px}
.slider-dots i{width:14px;height:14px;border:1px solid #c8c8c8;border-radius:50%;background:#f4f4f4;position:relative}
.slider-dots i.on::after{content:"";position:absolute;left:4px;top:4px;width:4px;height:4px;border-radius:50%;background:var(--navy)}

.section-ribbon{position:absolute;left:428px;top:535px;width:306px;height:52px}
.section-ribbon h2{position:absolute;left:33px;top:0;width:239px;height:41px;font-family:'Questrial',sans-serif;font-weight:400;font-size:27px;color:var(--white);text-align:center;line-height:43px}

.services{position:absolute;left:151px;top:650px;width:900px;display:grid;grid-template-columns:326px 325px 249px;row-gap:57px}
.service h3{display:flex;align-items:center;gap:10px;font-family:'Questrial',sans-serif;font-weight:400;font-size:18px;color:var(--navy);height:26px}
.service p{margin-top:10px;font-size:11.6px;line-height:15.3px;color:var(--text);width:240px}

.site-footer{position:absolute;left:0;top:937px;width:1200px;height:98px;background:var(--footer);border-top:1px solid #ececec}
.footer-links{position:absolute;left:149px;top:40px;font-size:11px;color:#666}
.footer-links a{color:#555;text-decoration:none}
.footer-links .bar{margin:0 6px;color:#888}
.social{position:absolute;left:965px;top:40px;display:flex;gap:5px}
.social span{width:18px;height:18px;border-radius:50%;background:#6a6a6a}
</style>
</head>
<body>

<header class="site-header">
  <div class="brand"><span class="brand-mark"></span>DVQ</div>
  <nav class="main-nav">
    <a class="active" href="#">Home</a>
    <a href="#">Services</a>
    <a href="#">Project</a>
    <a href="#">Articles</a>
    <a href="#">Contact</a>
  </nav>
  <div class="account">
    <span><svg width="8" height="9" viewBox="0 0 8 9"><rect x="0" y="4" width="8" height="5" fill="#a0a0a0"/><path d="M2 4V2.5a2 2 0 0 1 4 0V4" fill="none" stroke="#a0a0a0" stroke-width="1.2"/></svg>Log in</span>
    <span class="sep"></span>
    <span><svg width="9" height="9" viewBox="0 0 9 9"><path d="M1 8l1.5-.3L8 2.2 6.8 1 1.3 6.5z" fill="none" stroke="#a0a0a0"/></svg>Sign up</span>
  </div>
</header>

<section class="hero">
  <div class="hero-photo" role="img" aria-label="Photo of a smiling young professional in glasses and a striped shirt in a bright office"></div>
  <div class="hero-copy">
    <h1 class="hero-title">Welcome to Datavoque</h1>
    <p class="hero-lead">DVQ is a technology company providing<br>approachable IT products and services to business.</p>
    <a class="btn-more" href="#">LEARN MORE</a>
  </div>
  <div class="slider-dots"><i></i><i class="on"></i><i></i><i></i></div>
</section>

<div class="section-ribbon">
  <svg width="306" height="52" viewBox="0 0 306 52">
    <polygon points="0,10 42,10 42,51 0,51 10,30" fill="var(--navy-dark)"/>
    <polygon points="306,10 264,10 264,51 306,51 296,30" fill="var(--navy-dark)"/>
    <polygon points="33,41 42,41 42,51" fill="#1c2754"/>
    <polygon points="273,41 264,41 264,51" fill="#1c2754"/>
    <rect x="33" y="0" width="240" height="41" fill="var(--navy)"/>
  </svg>
  <h2>OUR SERVICES</h2>
</div>

<section class="services">
  <article class="service">
    <h3><svg width="25" height="22" viewBox="0 0 25 22"><rect x="1" y="1" width="23" height="15" fill="none" stroke="var(--navy)" stroke-width="2"/><rect x="10" y="16" width="5" height="4" fill="var(--navy)"/><rect x="6" y="20" width="13" height="2" fill="var(--navy)"/></svg>IT infrustucture</h3>
    <p>Lorem Ipsum is simply dummy text of the printing and typesetting industry. Lorem Ipsum dummy text ever since the 1500s...</p>
  </article>
  <article class="service">
    <h3><svg width="18" height="22" viewBox="0 0 18 22"><rect x="1" y="1" width="16" height="20" rx="2" fill="none" stroke="var(--navy)" stroke-width="2"/><circle cx="9" cy="17.5" r="1" fill="var(--navy)"/></svg>Devices</h3>
    <p>Lorem Ipsum is simply dummy text of the printing and typesetting industry. Lorem Ipsum dummy text ever since the 1500s...</p>
  </article>
  <article class="service">
    <h3><svg width="26" height="24" viewBox="0 0 26 24"><polygon points="13,1 25,6 13,11 1,6" fill="#4a5a96"/><polygon points="1,6 13,11 13,23 1,18" fill="var(--navy)"/><polygon points="25,6 13,11 13,23 25,18" fill="var(--navy-dark)"/></svg>Software</h3>
    <p>Lorem Ipsum is simply dummy text of the printing and typesetting industry. Lorem Ipsum dummy text ever since the 1500s...</p>
  </article>
  <article class="service">
    <h3><svg width="16" height="24" viewBox="0 0 16 24"><rect x="0" y="0" width="16" height="2" fill="var(--navy)"/><rect x="0" y="22" width="16" height="2" fill="var(--navy)"/><path d="M2 2c0 7 5 8 5 10s-5 3-5 10h12c0-7-5-8-5-10s5-3 5-10" fill="none" stroke="var(--navy)" stroke-width="1.6"/><polygon points="4,21 12,21 8,16" fill="var(--navy)"/></svg>Installation</h3>
    <p>Lorem Ipsum is simply dummy text of the printing and typesetting industry. Lorem Ipsum dummy text ever since the 1500s...</p>
  </article>
  <article class="service">
    <h3><svg width="22" height="24" viewBox="0 0 22 24"><path d="M5 23l-3-9 2-1 3 4V3a1.5 1.5 0 0 1 3 0v8V1.5a1.5 1.5 0 0 1 3 0V11V3a1.5 1.5 0 0 1 3 0v9V6a1.5 1.5 0 0 1 3 0v9l-3 8z" fill="var(--navy)"/></svg>Training</h3>
    <p>Lorem Ipsum is simply dummy text of the printing and typesetting industry. Lorem Ipsum dummy text ever since the 1500s...</p>
  </article>
  <article class="service">
    <h3><svg width="36" height="22" viewBox="0 0 36 22"><rect x="6" y="1" width="29" height="15" fill="none" stroke="var(--navy)" stroke-width="1.5"/><rect x="3" y="3.5" width="29" height="15" fill="#fff" stroke="var(--navy)" stroke-width="1.5"/><rect x="0.5" y="6" width="30" height="15" fill="var(--navy)"/><circle cx="15.5" cy="13.5" r="4.5" fill="#fff"/><rect x="14.5" y="10" width="2" height="7" fill="var(--navy)"/><circle cx="5" cy="13.5" r="1.5" fill="#fff"/><circle cx="26" cy="13.5" r="1.5" fill="#fff"/></svg>Cost control</h3>
    <p>Lorem Ipsum is simply dummy text of the printing and typesetting industry. Lorem Ipsum dummy text ever since the 1500s...</p>
  </article>
</section>

<footer class="site-footer">
  <div class="footer-links">
    <a href="#">Home</a><span class="bar">|</span><a href="#">Services</a><span class="bar">|</span><a href="#">Project</a><span class="bar">|</span><a href="#">Articles</a><span class="bar">|</span><a href="#">Contact</a><span class="bar">|</span>Copyright © 2013 Datavoque.
  </div>
  <div class="social"><span></span><span></span><span></span><span></span></div>
</footer>

</body>
</html>
```